Professional & attention grabbing.

A business card design, front and back. I already have a logo I will attach, but I am open to something new as well.
Things to include:
Name:
Title:
Phone:
Email:
Wanting something that is professional but attention grabbing.
Also we do a lot of work using drones on natural gas pipelines (leading the future)if you want to include any of that. I'm open to ideas.
Target Market(s)
Natural gas transmission industry / greenhouse gas mitigation industry
Industry/Entity Type
Business
Colors
Designer to choose colors to be used in the design.
Look and feel
Each slider illustrates characteristics of the customer's brand and the style your logo design should communicate.

```html
<!DOCTYPE html>
<html lang="en">
<head>
<meta charset="utf-8">
<title>TQ Field Inspections – Business Card</title>
<link href="https://fonts.googleapis.com/css2?family=Open+Sans:wght@400;600;700&display=swap" rel="stylesheet">
<style>
  :root {
    --backdrop: #5a4030;
    --card-dark: #1c1c1c;
    --brand-red: #c02026;
    --paper-white: #ffffff;
    --shadow: rgba(0,0,0,0.45);
  }
  html, body {
    margin: 0;
    padding: 0;
    width: 1200px;
    height: 1000px;
    overflow: hidden;
    background: var(--backdrop);
    font-family: "Open Sans", Arial, sans-serif;
  }
  .canvas {
    position: relative;
    width: 1200px;
    height: 1000px;
  }
  .card {
    position: absolute;
    left: 266px;
    width: 666px;
    height: 397px;
    box-shadow: 0 4px 14px var(--shadow);
  }
  .card--front { top: 74px; background: var(--card-dark); }
  .card--back { top: 534px; background: var(--brand-red); }

  /* Front: brand block */
  .front-brand {
    position: absolute;
    left: 97px;
    top: 102px;
    width: 190px;
    display: flex;
    flex-direction: column;
    align-items: flex-start;
    gap: 14px;
  }
  .front-brand__square {
    width: 110px;
    height: 110px;
    background: var(--brand-red);
  }
  .front-brand__name {
    color: var(--paper-white);
    font-weight: 700;
    font-size: 17px;
    line-height: 1.25;
    letter-spacing: 0.5px;
    text-transform: uppercase;
  }

  /* Front: contact details */
  .contact {
    position: absolute;
    left: 367px;
    top: 98px;
    color: var(--paper-white);
  }
  .contact__name {
    margin: 0;
    color: var(--brand-red);
    font-size: 21px;
    font-weight: 600;
    letter-spacing: 0.6px;
    line-height: 28px;
  }
  .contact__title {
    margin: 0 0 22px;
    font-size: 16px;
    line-height: 22px;
  }
  .contact__address {
    margin: 0 0 10px;
    font-style: normal;
    font-size: 16px;
    line-height: 25px;
  }
  .contact__list {
    list-style: none;
    margin: 0;
    padding: 0;
    font-size: 16px;
    line-height: 24.5px;
  }
  .contact__item {
    display: flex;
    align-items: center;
    gap: 7px;
  }
  .contact__icon {
    width: 15px;
    height: 15px;
    fill: var(--brand-red);
    flex: none;
  }

  /* Back: brand lockup */
  .back-brand {
    position: absolute;
    left: 0;
    right: 0;
    top: 123px;
    display: flex;
    align-items: center;
    justify-content: center;
    gap: 26px;
  }
  .back-brand__square {
    width: 150px;
    height: 150px;
    background: var(--paper-white);
  }
  .back-brand__name {
    color: var(--paper-white);
    font-weight: 700;
    font-size: 34px;
    line-height: 1.15;
    letter-spacing: 0.5px;
    text-transform: uppercase;
  }
</style>
</head>
<body>
<main class="canvas">
  <section class="card card--front" aria-label="Card front">
    <div class="front-brand">
      <div class="front-brand__square"></div>
      <div class="front-brand__name">TQ Field<br>Inspections</div>
    </div>
    <div class="contact">
      <h1 class="contact__name">DARON MEISEL</h1>
      <p class="contact__title">Managing Director</p>
      <address class="contact__address">4120 North Alder Lane<br>Hagerstown, MD 21740</address>
      <ul class="contact__list">
        <li class="contact__item">
          <svg class="contact__icon" viewBox="0 0 16 16" aria-hidden="true"><path d="M3 4c0-1.5 2-2.5 5-2.5S13 2.5 13 4v1.5h-2.5V4.3C9.8 4 6.2 4 5.5 4.3v1.2H3z"/><path d="M5 6.5h6l2.5 6.5H2.5z"/></svg>
          <span>+ 000 000 0000</span>
        </li>
        <li class="contact__item">
          <svg class="contact__icon" viewBox="0 0 16 16" aria-hidden="true"><path d="M1.5 4h13v1l-6.5 4.2L1.5 5z"/><path d="M1.5 6.2l6.5 4.2 6.5-4.2V12h-13z"/></svg>
          <span>info@TQfieldinspect.com</span>
        </li>
        <li class="contact__item">
          <svg class="contact__icon" viewBox="0 0 16 16" aria-hidden="true"><path d="M8 1.5a6.5 6.5 0 1 0 0 13 6.5 6.5 0 0 0 0-13zm0 1.8c.9 0 1.8 1.7 2 3.7H6c.2-2 1.1-3.7 2-3.7zM3.4 9h2.5c.1 1.4.4 2.6.9 3.4A4.8 4.8 0 0 1 3.4 9zm6.7 0h2.5a4.8 4.8 0 0 1-3.4 3.4c.5-.8.8-2 .9-3.4z"/></svg>
          <span>www.TQfieldinspect.com</span>
        </li>
      </ul>
    </div>
  </section>

  <section class="card card--back" aria-label="Card back">
    <div class="back-brand">
      <div class="back-brand__square"></div>
      <div class="back-brand__name">TQ Field<br>Inspections</div>
    </div>
  </section>
</main>
</body>
</html>
```